TORV Business Card Neil

Field Capital Advisory (TORV) is a consulting company that advises stakeholders in the Agricultural Industry. Based in rural NSW Australia, we need a good business card. TORV has a lifetime of agricultural experience and knowledge, particularly in the beef, wool and lamb markets. Though it is expanding into other rural ventures. Our clients are primarily off-farm investors who trust our business to advise on the best path forward for their agricultural investment. We also work with large players in the retail sector. Our image is trustworthy, reliable, smart and professional.
Updates

I think the black is too urban, perhaps a dark blue on one side and white on the other, or the yellow/orange on one side and white on the other??

we need to have the tag line "Customised Agribusiness Strategy" and our list of services:

"Due Diligence, Acquisition, Planning, Management, Strategy, Supply Chain" included in the design

we actually have 6 services - the should read in order:

Due diligence
Acquisition
Strategy
Planning 
Management
Supply chain

Target Market(s)

large rural land holders
senior players in agribusiness
senior management of retail food outlets
middle-senior aged men

Industry/Entity Type

Retail

Requirements
Must have
• high quality, 2 sides

logo

"Neil Ashcombe
Director
0413952617
neil@torv.com.au
PO Box 4721, Kelvale NSW 2361"

tag line "Customised Agribusiness Strategy"

services provided

"Due diligence
Acquisition
Strategy
Planning
Management
Supply chain"
Should not have
• no images of animals or leaves

```html
<!DOCTYPE html>
<html lang="en">
<head>
<meta charset="utf-8">
<title>TORV Business Card – Neil Ashcombe</title>
<link rel="stylesheet" href="https://fonts.googleapis.com/css2?family=Cinzel:wght@400;600&family=Libre+Baskerville&family=Merriweather+Sans:wght@400;700&display=swap">
<style>
  :root{
    --stage:#e9e9ea;
    --gold-deep:#f2a100;
    --gold-mid:#f8c91a;
    --gold-light:#f7ee2a;
    --brand-blue:#2d4ca6;
    --ink-grey:#5a5a5e;
    --name-amber:#f0ad2c;
    --tag-orange:#f0a218;
    --paper:#ffffff;
    --icon:#ffffff;
  }
  *{box-sizing:border-box;margin:0;padding:0}
  html,body{width:1200px;height:1024px;overflow:hidden}
  body{
    background:var(--stage);
    display:flex;flex-direction:column;align-items:center;justify-content:space-evenly;
    font-family:"Libre Baskerville",Georgia,serif;
  }
  .card{
    width:760px;height:464px;position:relative;overflow:hidden;
    box-shadow:0 6px 18px rgba(0,0,0,.18);
  }

  /* Front */
  .card--front{
    background:linear-gradient(120deg,var(--gold-deep) 0%,var(--gold-mid) 35%,var(--gold-light) 65%,var(--gold-mid) 100%);
  }
  .front__brand{position:absolute;left:60px;top:92px;}
  .brand-word{
    font-family:"Cinzel",Georgia,serif;font-weight:600;color:var(--brand-blue);
    letter-spacing:.04em;line-height:1;
  }
  .front__brand .brand-word{font-size:92px}
  .brand-sub{
    font-family:"Cinzel",Georgia,serif;color:var(--brand-blue);
    text-transform:uppercase;letter-spacing:.08em;
  }
  .front__brand .brand-sub{font-size:14px;margin-top:6px}
  .front__person{position:absolute;right:64px;top:110px;text-align:left;}
  .person-name{
    font-family:"Cinzel",Georgia,serif;font-size:36px;color:var(--name-amber);
    letter-spacing:.03em;text-transform:uppercase;
  }
  .person-title{
    font-family:"Cinzel",Georgia,serif;font-size:20px;color:var(--brand-blue);
    letter-spacing:.04em;margin-top:6px;padding-left:40px;
  }
  .front__rule{
    position:absolute;left:40px;right:40px;top:246px;border-top:2px dashed rgba(255,255,255,.9);
  }
  .contact-list{position:absolute;left:60px;top:282px;list-style:none;}
  .contact-list li{
    display:flex;align-items:center;gap:16px;
    font-size:21px;color:var(--ink-grey);height:42px;
  }
  .contact-list svg{width:22px;height:22px;flex:none}

  /* Back */
  .card--back{background:var(--paper);}
  .back__edge{position:absolute;left:0;top:0;bottom:0;width:34px;
    background:linear-gradient(180deg,var(--gold-mid),var(--gold-deep));}
  .back__brand{position:absolute;right:70px;top:52px;text-align:left;}
  .back__brand .brand-word{font-size:128px}
  .back__brand .brand-sub{font-size:19px;margin-top:8px;color:var(--ink-grey)}
  .tagline{
    position:absolute;left:92px;top:246px;
    font-family:"Merriweather Sans",Arial,sans-serif;font-weight:700;font-size:22px;
    color:var(--tag-orange);
  }
  .services{position:absolute;left:92px;top:306px;
    font-family:"Merriweather Sans",Arial,sans-serif;font-size:21px;color:var(--ink-grey);line-height:1.9;}
  .services .sep{color:var(--tag-orange);padding:0 10px}
</style>
</head>
<body>

  <section class="card card--front" aria-label="Business card front">
    <div class="front__brand">
      <div class="brand-word">TORV</div>
      <div class="brand-sub">Field Capital Advisory</div>
    </div>
    <div class="front__person">
      <div class="person-name">Neil Ashcombe</div>
      <div class="person-title">DIRECTOR</div>
    </div>
    <div class="front__rule"></div>
    <ul class="contact-list">
      <li>
        <svg viewBox="0 0 24 24" aria-hidden="true"><rect x="6" y="2" width="12" height="20" rx="2" fill="var(--icon)"/><rect x="8" y="5" width="8" height="12" fill="var(--gold-mid)"/></svg>
        0413 952 617
      </li>
      <li>
        <svg viewBox="0 0 24 24" aria-hidden="true"><rect x="2" y="5" width="20" height="14" fill="var(--icon)"/><path d="M2 5l10 8 10-8" fill="none" stroke="var(--gold-mid)" stroke-width="1.6"/></svg>
        neil@torv.com.au
      </li>
      <li>
        <svg viewBox="0 0 24 24" aria-hidden="true"><path d="M12 2a7 7 0 0 0-7 7c0 5 7 13 7 13s7-8 7-13a7 7 0 0 0-7-7z" fill="var(--icon)"/><circle cx="12" cy="9" r="2.6" fill="var(--gold-mid)"/></svg>
        PO Box 4721, Kelvale NSW 2361
      </li>
    </ul>
  </section>

  <section class="card card--back" aria-label="Business card back">
    <div class="back__edge"></div>
    <div class="back__brand">
      <div class="brand-word">TORV</div>
      <div class="brand-sub">Field Capital Advisory</div>
    </div>
    <p class="tagline">Customised Agribusiness Strategy</p>
    <div class="services">
      <div>Due diligence<span class="sep">|</span>Acquisition</div>
      <div>Strategy<span class="sep">|</span>Planning<span class="sep">|</span>Management<span class="sep">|</span>Supply chain</div>
    </div>
  </section>

</body>
</html>
```